Business Card Design Project

We're looking for a unique business card design that stands out from the rest, using the brand and logo we've already developed.
Two-sided design please.
Quillmark Media (www.quillmarkmedia.com.au) is a digitally-focused advertising agency that has produces results-driven campaigns. As a result, we'd like our business card to reflect our innovative approach.
Size, shape, orientation, etc, are all flexible (providing the print costs don't become ridiculous or we have to sit there with tiny scissors!).
Business card should include space for name, title, email, mobile, landline and address.
Industry/Entity Type
Advertising
Look and feel

```html
<!DOCTYPE html>
<html lang="en">
<head>
<meta charset="utf-8">
<title>Quillmark Media — Business Card</title>
<link rel="stylesheet" href="https://fonts.googleapis.com/css2?family=Michroma&display=swap">
<style>
  :root {
    --backdrop: #3b2717;
    --card-white: #ffffff;
    --brand-orange: #f26722;
    --accent-orange: #f7931e;
    --ink-black: #000000;
    --label-white: #ffffff;
  }
  * { margin: 0; padding: 0; box-sizing: border-box; }
  html, body {
    width: 1200px;
    height: 1200px;
    overflow: hidden;
    background: var(--backdrop);
    font-family: "Michroma", sans-serif;
  }
  .canvas { position: relative; width: 1200px; height: 1200px; }

  .card {
    position: absolute;
    border-radius: 17px;
    overflow: hidden;
  }

  /* Front */
  .card-front {
    left: 116px; top: 72px; width: 900px; height: 516px;
    background: linear-gradient(to bottom, var(--card-white) 0 258px, var(--brand-orange) 258px 100%);
  }
  .front-wordmark {
    position: absolute;
    left: 0; right: 0; top: 222px;
    text-align: center;
    font-size: 58px;
    line-height: 72px;
    color: var(--ink-black);
    letter-spacing: 2px;
  }

  /* Back */
  .card-back {
    left: 126px; top: 612px; width: 898px; height: 518px;
    background: var(--brand-orange);
  }
  .back-header {
    position: absolute; left: 0; top: 0; width: 100%; height: 186px;
    background: var(--ink-black);
  }
  .header-stripe {
    position: absolute; left: 0; top: 186px; width: 100%; height: 16px;
    background: var(--accent-orange);
  }
  .back-wordmark {
    position: absolute; left: 0; right: 0; top: 62px;
    text-align: center;
    font-size: 50px;
    line-height: 64px;
    color: var(--card-white);
    letter-spacing: 2px;
  }
  .holder-name {
    position: absolute; left: 0; right: 0; top: 222px;
    text-align: center;
    font-size: 38px;
    line-height: 44px;
    color: var(--ink-black);
    letter-spacing: 6px;
  }
  .holder-title {
    position: absolute; left: 0; right: 0; top: 276px;
    text-align: center;
    font-size: 28px;
    line-height: 36px;
    font-weight: bold;
    color: var(--ink-black);
    letter-spacing: 2px;
  }
  .contact-label {
    position: absolute;
    font-size: 19px;
    line-height: 24px;
    color: var(--label-white);
    letter-spacing: 1px;
  }
  .label-email    { left: 66px;  top: 378px; }
  .label-mobile   { left: 66px;  top: 420px; }
  .label-landline { left: 462px; top: 386px; }
  .label-address  { left: 466px; top: 426px; }
</style>
</head>
<body>
  <main class="canvas">
    <section class="card card-front" aria-label="Card front">
      <div class="front-wordmark">Quillmark Media</div>
    </section>

    <section class="card card-back" aria-label="Card back">
      <div class="back-header"></div>
      <div class="header-stripe"></div>
      <div class="back-wordmark">Quillmark Media</div>
      <div class="holder-name">NAME</div>
      <div class="holder-title">TITLE</div>
      <div class="contact-label label-email">EMAIL:</div>
      <div class="contact-label label-mobile">MOBILE:</div>
      <div class="contact-label label-landline">LANDLINE:</div>
      <div class="contact-label label-address">ADDRESS:</div>
    </section>
  </main>
</body>
</html>
```